Looking to build a senior life alert web page

We definitely want to incorporate pictures of the product in which we're selling and want colors that resonate with the senior community. We're looking for something also clean and very easy to navigate. We're looking to pick a design immediately!
Based on something similar to that of our competition which can be located at the following
https://www.tovrelcarelink.example/
https://www.wellkestrix.example/

attached is the product we're selling

The name of our company is the golden harbor circle

Target Market(s)

Elderly people looking for a life alert device

Industry/Entity Type

Medical Equipment

Number of Pages Required

3 page

Font styles to use
Serif

Colors

Designer to choose colors to be used in the design.

Requirements
Must have
• Pictures of the product a nice UI experience that can be easily made mobile friendly
Nice to have
• Including area for video content maybe / friendly color LOGOS are attached for our company

```html
<!DOCTYPE html>
<html lang="en">
<head>
<meta charset="utf-8">
<title>Golden Harbor Circle</title>
<link rel="stylesheet" href="https://fonts.googleapis.com/css2?family=Cinzel:wght@400;600;700&family=Roboto:wght@400;500;700&display=swap">
<style>
:root{
  --orange:#e8702a;
  --orange-light:#f39a3c;
  --orange-deep:#d95f1f;
  --navy:#1e4a75;
  --navy-dark:#163a5e;
  --ink:#2a2a2a;
  --muted:#8a8a8a;
  --line:#e2e2e2;
  --white:#ffffff;
  --sky:#dfe8f0;
}
*{box-sizing:border-box;margin:0;padding:0}
html,body{width:1200px;height:4000px;overflow:hidden;background:var(--white)}
body{font-family:"Roboto",Arial,sans-serif;color:var(--ink);position:relative}
.serif{font-family:"Cinzel",Georgia,serif}
.wrap{width:1000px;margin:0 auto;position:relative}

/* header */
.site-header{height:120px;position:relative}
.brand{position:absolute;left:100px;top:14px;display:flex;flex-direction:column;align-items:center;width:200px}
.brand-dot{width:50px;height:50px;border-radius:50%;background:var(--orange)}
.brand-name{font-family:"Cinzel",Georgia,serif;font-weight:700;font-size:17px;color:var(--navy);margin-top:6px;text-align:center;line-height:1.1}
.topbar{position:absolute;right:100px;top:24px;display:flex;align-items:center;gap:8px;font-size:13px;color:var(--ink)}
.topbar strong{font-weight:700;margin-right:8px}
.social{display:flex;gap:6px}
.social span{width:26px;height:26px;border-radius:50%;background:var(--navy);display:block}
.social span:nth-child(3),.social span:nth-child(5){background:var(--orange)}
.main-nav{position:absolute;right:100px;top:68px;display:flex;align-items:center;gap:38px;font-size:13px;font-weight:500;color:var(--navy)}
.nav-home{width:48px;height:48px;border-radius:50%;border:3px solid var(--navy);display:flex;align-items:center;justify-content:center;font-size:11px;color:var(--navy)}
.nav-cart{width:34px;height:34px;border-radius:50%;border:2px solid var(--orange);display:flex;align-items:center;justify-content:center}

/* hero */
.hero{height:520px;position:relative;overflow:hidden;background:linear-gradient(180deg,#e8702a 0%,#f29a33 55%,#f6b43e 80%,#c96a22 100%)}
.hero-crowd{position:absolute;left:0;right:0;top:340px;height:110px;background:linear-gradient(180deg,rgba(20,20,20,.0),#1b1b1b 60%)}
.hero-title{position:absolute;left:100px;top:112px;color:var(--white);font-family:"Cinzel",Georgia,serif}
.hero-title h1{font-weight:400;font-size:42px;letter-spacing:1px}
.hero-title p{font-size:30px;letter-spacing:8px;margin-top:6px}
.btn{display:inline-block;border-radius:30px;font-size:13px;font-weight:700;text-align:center}
.btn-hero{position:absolute;left:100px;top:244px;background:var(--navy);color:var(--white);padding:14px 30px}
.hero-device{position:absolute;left:830px;top:40px;width:300px;height:330px;border-radius:30px;background:linear-gradient(160deg,#f3d8c2,#e9e5e2 60%,#cfc7c2)}
.hero-wave{position:absolute;left:0;bottom:0;width:1200px;height:100px}
.hero-dots{position:absolute;left:560px;top:470px;display:flex;gap:8px}
.hero-dots i{width:10px;height:10px;border-radius:50%;border:2px solid var(--white);display:block}
.hero-dots i:first-child{background:var(--orange);border-color:var(--orange)}

/* section headings */
.eyebrow{display:flex;align-items:center;gap:14px;font-family:"Cinzel",Georgia,serif}
.eyebrow::before,.eyebrow::after{content:"";height:2px;width:56px;background:currentColor;opacity:.6}
.section-title{justify-content:center;font-size:34px;font-weight:600}

/* about */
.about{height:530px;position:relative}
.about-text{position:absolute;left:100px;top:92px;width:560px}
.about-text .small-title{font-family:"Cinzel",Georgia,serif;color:var(--orange);font-size:32px;font-weight:600;padding-left:60px;position:relative}
.about-text .small-title::before{content:"";position:absolute;left:0;top:22px;width:50px;height:2px;background:var(--orange)}
.about-text .big-title{font-family:"Cinzel",Georgia,serif;color:var(--navy);font-size:26px;font-weight:600;margin:6px 0 0 60px;position:relative}
.about-text .big-title::after{content:"";position:absolute;right:-60px;top:18px;width:48px;height:2px;background:var(--navy)}
.about-text p{font-size:12px;line-height:33px;color:var(--muted);margin-top:20px}
.about-actions{display:flex;gap:16px;margin-top:22px}
.btn-solid{background:var(--orange);color:var(--white);padding:14px 30px}
.btn-outline{border:2px solid var(--line);color:var(--navy);padding:12px 28px}
.about-art{position:absolute;left:700px;top:70px;width:400px;height:400px;border-radius:50%;background:radial-gradient(circle,#ffffff 55%,#dbe3ea 56%,#dbe3ea 70%,#ffffff 71%)}

/* products */
.products{height:565px;background:linear-gradient(135deg,var(--navy-dark),#2b5a88 50%,var(--navy-dark));position:relative}
.products .section-title{color:var(--white);padding-top:84px}
.product-row{position:absolute;left:100px;top:150px;width:1000px;height:312px;display:flex}
.card{flex:1;display:flex;flex-direction:column;align-items:center;padding-top:32px}
.card-light{background:var(--white)}
.card-accent{background:var(--orange);color:var(--white)}
.card h3{font-size:18px;font-weight:500;color:var(--navy)}
.card-accent h3{color:var(--white);font-size:16px;margin-top:14px}
.card-photo{width:130px;height:130px;margin-top:18px;border-radius:10px;background:linear-gradient(160deg,#f1f1f1,#d9d9d9)}
.card p{font-size:11px;line-height:20px;text-align:center;width:190px;margin-top:12px}
.card .btn{margin-top:auto;margin-bottom:40px;font-size:12px;padding:10px 26px}
.card-light .btn{border:2px solid var(--orange);color:var(--orange)}
.card-accent .btn{border:2px solid var(--white);color:var(--white)}
.card-accent .btn:first-of-type{margin-top:26px}
.products-badge{position:absolute;left:572px;top:440px;width:56px;height:56px;border-radius:50%;background:var(--white);border:6px solid var(--orange)}

/* news */
.news{height:1200px;position:relative}
.news .section-title{color:var(--orange);padding-top:80px}
.news-item{position:absolute;width:1000px;left:100px;height:320px}
.news-photo{position:absolute;top:0;width:500px;height:320px;border-top:4px solid var(--navy)}
.news-photo .play{position:absolute;left:224px;top:134px;width:54px;height:54px;border-radius:50%;background:#e02b2b;display:flex;align-items:center;justify-content:center}
.news-body{position:absolute;top:56px;width:450px}
.news-body h3{font-size:20px;font-weight:500;color:var(--navy)}
.news-date{font-size:11px;color:var(--navy);margin-top:14px;display:flex;align-items:center;gap:6px}
.news-body p{font-size:11px;line-height:24px;color:var(--muted);margin-top:10px}
.news-body .btn{margin-top:18px;border:2px solid var(--orange);color:var(--orange);padding:9px 24px;font-size:12px;font-weight:500}
.news-mark{position:absolute;width:56px;height:56px;border-radius:50%;background:var(--white);border:5px solid var(--orange);box-shadow:0 0 0 4px var(--white)}

/* testimonials */
.testimonials{height:520px;position:relative;background:linear-gradient(90deg,#e06726,#ef8a3a 50%,#e06726)}
.testimonials .section-title{color:var(--white);padding-top:64px}
.testimonials-deco{position:absolute;left:40px;top:80px;width:220px;height:340px;border-radius:30px;background:rgba(255,255,255,.12)}
.avatar{position:absolute;left:556px;top:132px;width:88px;height:88px;border-radius:50%;background:var(--sky);border:5px solid var(--navy)}
.quote{position:absolute;left:250px;top:260px;width:700px;text-align:center;color:var(--white);font-size:12px;line-height:30px}
.quote-mark{position:absolute;font-family:Georgia,serif;font-size:60px;color:var(--white);line-height:1}
.author{position:absolute;left:0;right:0;top:370px;text-align:center;color:var(--white);font-size:12px;font-weight:700}
.author .stars{color:#ffd23a;letter-spacing:2px;margin-left:6px}
.t-dots{position:absolute;left:584px;top:402px;display:flex;gap:6px}
.t-dots i{width:8px;height:8px;border-radius:50%;background:rgba(255,255,255,.6);display:block}
.t-dots i:first-child{background:var(--white)}

/* contact */
.contact{height:465px;position:relative}
.contact .section-title{color:var(--orange);padding-top:72px}
.get-in-touch{position:absolute;left:100px;top:132px;width:606px}
.col-title{font-size:15px;font-weight:500;color:var(--ink)}
.form-row{display:flex;gap:12px;margin-top:18px}
.field{flex:1;height:32px;border:1px solid var(--line);font-size:10px;color:var(--muted);padding:9px 12px}
.field-message{height:72px}
.btn-submit{position:absolute;right:0;top:250px;background:var(--navy);color:var(--white);padding:11px 24px;font-size:12px}
.contact-info{position:absolute;left:760px;top:132px;width:340px}
.info-line{display:flex;align-items:flex-start;gap:14px;margin-top:18px;font-size:11px;line-height:18px;color:var(--ink);width:210px}
.info-icon{flex:none;width:34px;height:34px;border-radius:50%;border:1px solid var(--line);display:flex;align-items:center;justify-content:center}
.contact-info .social{margin-top:18px}
.contact-art{position:absolute;left:990px;top:190px;width:180px;height:200px;border-radius:50%;background:radial-gradient(circle,#f4efe9 55%,#e3e8ee 56%)}

/* footer */
.site-footer{position:absolute;left:100px;top:3920px;width:1000px;height:80px;border-top:1px solid var(--line);text-align:center;font-size:11px;color:var(--ink);padding-top:28px}
</style>
</head>
<body>

<header class="site-header">
  <div class="brand">
    <span class="brand-dot"></span>
    <span class="brand-name">Golden Harbor Circle</span>
  </div>
  <div class="topbar">
    <svg width="14" height="14" viewBox="0 0 24 24"><path d="M6.6 10.8a15 15 0 0 0 6.6 6.6l2.2-2.2a1 1 0 0 1 1-.25 11 11 0 0 0 3.6.6 1 1 0 0 1 1 1V20a1 1 0 0 1-1 1A17 17 0 0 1 3 4a1 1 0 0 1 1-1h3.5a1 1 0 0 1 1 1 11 11 0 0 0 .6 3.6 1 1 0 0 1-.25 1z" fill="#1e4a75"/></svg>
    <span>CALL US :</span><strong>1 800 555 0142</strong>
    <div class="social"><span></span><span></span><span></span><span></span><span></span></div>
  </div>
  <nav class="main-nav">
    <span class="nav-home">HOME</span>
    <span>ABOUT US</span>
    <span>PRODUCTS</span>
    <span>HOW IT WORKS</span>
    <span>NEWS</span>
    <span>CONTACT US</span>
    <span class="nav-cart"><svg width="16" height="16" viewBox="0 0 24 24"><path d="M3 4h3l2 11h11l2-8H7" fill="none" stroke="#e8702a" stroke-width="2"/><circle cx="10" cy="19" r="1.6" fill="#e8702a"/><circle cx="17" cy="19" r="1.6" fill="#e8702a"/></svg></span>
  </nav>
</header>

<section class="hero">
  <div class="hero-crowd" role="img" aria-label="Silhouettes of a row of people holding hands against a sunset sky"></div>
  <div class="hero-title"><h1>GOLDEN HARBOR</h1><p>CIRCLE</p></div>
  <span class="btn btn-hero">CHOOSE YOUR DEVICE</span>
  <div class="hero-device" role="img" aria-label="A hand holding the white alert pendant with a red cross button and a special offer tag"></div>
  <svg class="hero-wave" viewBox="0 0 1200 100" preserveAspectRatio="none"><path d="M0 40 Q600 130 1200 40 L1200 100 L0 100Z" fill="#163a5e"/><path d="M0 62 Q600 140 1200 62 L1200 100 L0 100Z" fill="#ffffff"/></svg>
  <div class="hero-dots"><i></i><i></i><i></i><i></i><i></i></div>
</section>

<section class="about">
  <div class="about-text">
    <div class="small-title">About</div>
    <div class="big-title">Golden Harbor Circle</div>
    <p>Our alert pendants give seniors a simple way to reach help at any hour of the day or night. One press of the button connects you to a caring response team who can speak with you, call your family, or send emergency services to your door. Setup takes minutes, there are no long contracts, and the device is light, waterproof and easy to wear every day at home or out walking with friends.</p>
    <div class="about-actions"><span class="btn btn-solid">READ MORE</span><span class="btn btn-outline">CALL US NOW !</span></div>
  </div>
  <div class="about-art" role="img" aria-label="Illustration of a caregiver helping an elderly woman with a cane"></div>
</section>

<section class="products">
  <h2 class="eyebrow section-title">Our Products</h2>
  <div class="product-row">
    <div class="card card-light">
      <h3>Home Alert Pendant</h3>
      <div class="card-photo" role="img" aria-label="White alert pendant with red cross button and price tag"></div>
      <span class="btn">VIEW DETAILS</span>
    </div>
    <div class="card card-accent">
      <svg width="54" height="46" viewBox="0 0 54 46"><path d="M2 4h9l6 26h28l6-18H14" fill="none" stroke="#fff" stroke-width="3"/><circle cx="21" cy="39" r="4" fill="#fff"/><circle cx="40" cy="39" r="4" fill="#fff"/></svg>
      <h3>SHOP ONLINE</h3>
      <p>Order your device today and have it delivered ready to use within days.</p>
      <span class="btn">BUY NOW</span>
    </div>
    <div class="card card-light">
      <h3>Mobile Alert Button</h3>
      <div class="card-photo" role="img" aria-label="White alert button with red cross and price tag"></div>
      <span class="btn">VIEW DETAILS</span>
    </div>
    <div class="card card-accent">
      <svg width="44" height="44" viewBox="0 0 24 24"><path d="M6.6 10.8a15 15 0 0 0 6.6 6.6l2.2-2.2a1 1 0 0 1 1-.25 11 11 0 0 0 3.6.6 1 1 0 0 1 1 1V20a1 1 0 0 1-1 1A17 17 0 0 1 3 4a1 1 0 0 1 1-1h3.5a1 1 0 0 1 1 1 11 11 0 0 0 .6 3.6 1 1 0 0 1-.25 1z" fill="#fff"/></svg>
      <h3>RISK FREE DIAL</h3>
      <p>Try our service for thirty days and call our team with any question.</p>
      <span class="btn">CALL NOW !</span>
    </div>
  </div>
  <span class="products-badge"></span>
</section>

<section class="news">
  <h2 class="eyebrow section-title">Our Latest News</h2>

  <article class="news-item" style="top:175px">
    <div class="news-photo" style="left:0;background:linear-gradient(135deg,#c9a77a,#e9d7b8 50%,#8d9a5c)" role="img" aria-label="Video still of two senior women laughing together in a park">
      <span class="play"><svg width="18" height="18" viewBox="0 0 10 10"><path d="M2 1l7 4-7 4z" fill="#fff"/></svg></span>
    </div>
    <div class="news-body" style="left:530px">
      <h3>Staying independent with a simple alert</h3>
      <div class="news-date"><svg width="11" height="11" viewBox="0 0 10 10"><rect x="0.5" y="1.5" width="9" height="8" fill="none" stroke="#e8702a"/><path d="M0.5 4h9" stroke="#e8702a"/></svg>November 10,2017</div>
      <p>Many families tell us the pendant brings calm to daily life. Learn how one press of a button keeps help close while seniors enjoy their own homes and routines.</p>
      <span class="btn">READ MORE</span>
    </div>
  </article>
  <span class="news-mark" style="left:572px;top:467px"></span>

  <article class="news-item" style="top:495px">
    <div class="news-photo" style="left:500px;border-top:none;border-bottom:4px solid var(--orange);background:linear-gradient(135deg,#e4e4e4,#c7c9cc 50%,#e4e4e4)" role="img" aria-label="Video still of a group of people standing in a circle seen from above">
      <span class="play"><svg width="18" height="18" viewBox="0 0 10 10"><path d="M2 1l7 4-7 4z" fill="#fff"/></svg></span>
    </div>
    <div class="news-body" style="left:0">
      <h3>Building a circle of care around you</h3>
      <div class="news-date"><svg width="11" height="11" viewBox="0 0 10 10"><rect x="0.5" y="1.5" width="9" height="8" fill="none" stroke="#e8702a"/><path d="M0.5 4h9" stroke="#e8702a"/></svg>November 10,2017</div>
      <p>Add family and neighbours to your contact list so the right people hear from us first. Our team explains each step and keeps everyone informed and ready.</p>
      <span class="btn">READ MORE</span>
    </div>
  </article>
  <span class="news-mark" style="left:572px;top:787px"></span>

  <article class="news-item" style="top:815px">
    <div class="news-photo" style="left:0;background:linear-gradient(135deg,#d9cbb8,#f1ece4 50%,#a9b5c2)" role="img" aria-label="Video still of a woman helping an elderly woman read a document at home">
      <span class="play"><svg width="18" height="18" viewBox="0 0 10 10"><path d="M2 1l7 4-7 4z" fill="#fff"/></svg></span>
    </div>
    <div class="news-body" style="left:530px">
      <h3>Five questions to ask before you choose</h3>
      <div class="news-date"><svg width="11" height="11" viewBox="0 0 10 10"><rect x="0.5" y="1.5" width="9" height="8" fill="none" stroke="#e8702a"/><path d="M0.5 4h9" stroke="#e8702a"/></svg>November 10,2017</div>
      <p>Range, battery life and response time all matter. Here is a short guide to help you compare alert devices and pick the one that suits your daily life.</p>
      <span class="btn">READ MORE</span>
    </div>
  </article>
</section>

<section class="testimonials">
  <div class="testimonials-deco" role="img" aria-label="Faint large image of the alert pendant"></div>
  <h2 class="eyebrow section-title">What customers are saying</h2>
  <div class="avatar" role="img" aria-label="Portrait of a smiling customer"></div>
  <span class="quote-mark" style="left:248px;top:250px">&ldquo;</span>
  <p class="quote">Since my daughter set up the pendant I feel safe living on my own again. The team answered in seconds the one time I fell, stayed on the line with me, and called my son straight away. It is light, simple to wear and worth every penny for our peace of mind.</p>
  <span class="quote-mark" style="left:920px;top:326px">&rdquo;</span>
  <div class="author">- MARA ELLISON <span class="stars">★★★★★</span></div>
  <div class="t-dots"><i></i><i></i><i></i><i></i></div>
</section>

<section class="contact">
  <h2 class="eyebrow section-title">Contact Us</h2>
  <div class="get-in-touch">
    <div class="col-title">Get In Touch:</div>
    <div class="form-row"><span class="field">NAME *</span><span class="field">PHONE :</span></div>
    <div class="form-row"><span class="field">EMAIL *</span></div>
    <div class="form-row"><span class="field field-message">MESSAGE :</span></div>
    <span class="btn btn-submit">SUBMIT</span>
  </div>
  <div class="contact-info">
    <div class="col-title">Contact Info</div>
    <div class="info-line"><span class="info-icon"><svg width="12" height="14" viewBox="0 0 12 16"><path d="M6 0a6 6 0 0 0-6 6c0 4.5 6 10 6 10s6-5.5 6-10a6 6 0 0 0-6-6zm0 8.5A2.5 2.5 0 1 1 6 3.5a2.5 2.5 0 0 1 0 5z" fill="#1e4a75"/></svg></span><span>Help is ready for anyone who lives or travels alone.</span></div>
    <div class="info-line"><span class="info-icon"><svg width="13" height="13" viewBox="0 0 24 24"><path d="M6.6 10.8a15 15 0 0 0 6.6 6.6l2.2-2.2a1 1 0 0 1 1-.25 11 11 0 0 0 3.6.6 1 1 0 0 1 1 1V20a1 1 0 0 1-1 1A17 17 0 0 1 3 4a1 1 0 0 1 1-1h3.5a1 1 0 0 1 1 1 11 11 0 0 0 .6 3.6 1 1 0 0 1-.25 1z" fill="#1e4a75"/></svg></span><span style="padding-top:8px">Phone: 1 800 555 0142</span></div>
    <div class="info-line"><span class="info-icon"><svg width="14" height="11" viewBox="0 0 14 10"><rect x="0.5" y="0.5" width="13" height="9" fill="none" stroke="#1e4a75"/><path d="M0.5 0.5l6.5 5 6.5-5" fill="none" stroke="#1e4a75"/></svg></span><span style="padding-top:8px">hello@goldenharbor.example</span></div>
    <div class="social"><span></span><span></span><span></span><span></span><span></span></div>
  </div>
  <div class="contact-art" role="img" aria-label="Illustration of a caregiver walking with an elderly woman"></div>
</section>

<footer class="site-footer">Copyrights © 2017, Golden Harbor Circle. All Rights Reserved &nbsp;|&nbsp; Privacy policy</footer>

</body>
</html>
```